Business Card Design for Training Business

Clear Path Coaching is a new business that delivers training and other services with a focus on topics related to mental health and wellbeing, for example, Wellmind Response Course, Resilience etc. We have a strong focus on evidence-based psychology and neuroscience. I have a logo which I will upload with the brief, so please consider colours that work well with the logo.
Target Market(s)
Adults, workplaces (particularly government and not-for-profits)
Industry/Entity Type
Business
Contact Information for Business Card
Head Strong TrainingSamantha SellwoodDirector0438 770 850sam@headstrongtraining.com.auwww.headstrongtraining.com.au

```html
<!DOCTYPE html>
<html lang="en">
<head>
<meta charset="utf-8">
<title>Clear Path Coaching — Business Card</title>
<link rel="stylesheet" href="https://fonts.googleapis.com/css2?family=Open+Sans:wght@300;400;700&display=swap">
<style>
  :root {
    --page-bg: #e9e7e3;
    --card-black: #0d0d0d;
    --card-white: #f7f7f7;
    --teal: #3fbdbf;
    --rule-grey: #8a8a8a;
    --ink: #111111;
    --ink-soft: #3a3a3a;
    --logo-text: #d9d9d9;
  }
  * { margin: 0; padding: 0; box-sizing: border-box; }
  html, body {
    width: 1200px;
    height: 1022px;
    overflow: hidden;
    background: var(--page-bg);
    font-family: "Open Sans", Arial, sans-serif;
  }
  .business-card {
    position: absolute;
    left: 150px;
    top: 236px;
    width: 900px;
    height: 550px;
    border-radius: 28px;
    overflow: hidden;
    background: var(--card-black);
    box-shadow: 0 18px 40px rgba(0,0,0,0.25);
  }
  .card-shapes {
    position: absolute;
    inset: 0;
    width: 900px;
    height: 550px;
  }
  .brand {
    position: absolute;
    left: 56px;
    top: 300px;
    display: flex;
    align-items: center;
    gap: 20px;
    color: var(--logo-text);
    font-weight: 300;
  }
  .brand-mark {
    width: 66px;
    height: 66px;
    border-radius: 50%;
    border: 2px solid var(--teal);
    flex: none;
  }
  .brand-name { line-height: 1; }
  .brand-name .line-main {
    display: block;
    font-size: 34px;
    letter-spacing: 3px;
    white-space: nowrap;
  }
  .brand-name .line-sub {
    display: block;
    margin-top: 10px;
    font-size: 15px;
    letter-spacing: 8px;
    text-align: center;
  }
  .contact-block {
    position: absolute;
    right: 60px;
    top: 62px;
    text-align: right;
  }
  .person-name {
    font-size: 34px;
    font-weight: 700;
    color: var(--ink);
    letter-spacing: 0.3px;
    white-space: nowrap;
  }
  .person-role {
    font-size: 22px;
    font-weight: 400;
    color: var(--teal);
    margin-top: 2px;
  }
  .contact-icons {
    display: flex;
    justify-content: flex-end;
    gap: 12px;
    margin-top: 18px;
  }
  .contact-icons svg {
    width: 20px;
    height: 20px;
    stroke: var(--teal);
    fill: none;
    stroke-width: 1.8;
  }
  .contact-lines {
    margin-top: 58px;
    font-size: 18px;
    line-height: 1.5;
    color: var(--ink-soft);
    white-space: nowrap;
  }
  .contact-lines .phone { margin-bottom: 54px; font-size: 21px; }
</style>
</head>
<body>
  <div class="business-card">
    <svg class="card-shapes" viewBox="0 0 900 550" aria-hidden="true">
      <defs>
        <linearGradient id="blackSheen" x1="0" y1="0" x2="1" y2="1">
          <stop offset="0" stop-color="#000000"/>
          <stop offset="0.6" stop-color="#1a1a1a"/>
          <stop offset="1" stop-color="#2e2e2e"/>
        </linearGradient>
      </defs>
      <rect width="900" height="550" fill="url(#blackSheen)"/>
      <g transform="translate(-50 0)">
        <path class="accent-stripe" d="M452 0 C490 120 470 300 520 430 C545 495 590 535 660 550 L620 550 C560 530 520 490 498 430 C450 300 470 120 432 0 Z"
              fill="var(--teal)"/>
        <path class="accent-rule" d="M470 0 C505 120 488 300 536 428 C560 490 600 530 680 550"
              fill="none" stroke="var(--rule-grey)" stroke-width="3"/>
        <path class="info-panel" d="M478 0 L950 0 L950 550 L700 550 C615 530 570 490 548 428 C500 300 518 120 478 0 Z"
              fill="var(--card-white)"/>
      </g>
    </svg>

    <div class="brand">
      <span class="brand-mark"></span>
      <div class="brand-name">
        <span class="line-main">CLEAR PATH</span>
        <span class="line-sub">COACHING</span>
      </div>
    </div>

    <div class="contact-block">
      <div class="person-name">Rebecca Tanfield</div>
      <div class="person-role">Director</div>
      <div class="contact-icons">
        <svg viewBox="0 0 20 20"><path d="M5 2 L8 6 L6.5 8 C7.5 10.5 9.5 12.5 12 13.5 L14 12 L18 15 L16 18 C9 18 2 11 2 4 Z"/></svg>
        <svg viewBox="0 0 20 20"><rect x="2" y="4" width="16" height="12" rx="1"/><path d="M2 5 L10 11 L18 5"/></svg>
        <svg viewBox="0 0 20 20"><circle cx="10" cy="10" r="8"/><ellipse cx="10" cy="10" rx="3.5" ry="8"/><path d="M2 10 H18"/></svg>
      </div>
      <div class="contact-lines">
        <div class="phone">0491 362 517</div>
        <div class="email">bec@clearpathcoaching.example.au</div>
        <div class="web">www.clearpathcoaching.example.au</div>
      </div>
    </div>
  </div>
</body>
</html>
```